Company identity deisgn should support 2 languages

I would like to get our company identity design
This includes the following only
Business Cards 2 languages Arabic and English
Email signature
Letterhead
Linkedin profile images
Attached is the logo in Ai format

Requirements
Must have
• For business card
Must have
Name and Adrees in arabic
Name and Address in english
You might use both side of the card
Should not have
• Any pictures other than the logo

```html
<!DOCTYPE html>
<html lang="en">
<head>
<meta charset="utf-8">
<title>Qamar Data Systems – Identity</title>
<link rel="stylesheet" href="https://fonts.googleapis.com/css2?family=Open+Sans:wght@400;600;700&family=Roboto:wght@400;500;700&family=Noto+Sans+Arabic:wght@400;600&display=swap">
<style>
:root{
  --blue:#1a73c4;
  --blue-dark:#1262b0;
  --blue-light:#2a9ad8;
  --grey-band:#6d6e71;
  --ink:#333;
  --muted:#555;
  --stage:#2c2c2e;
  --page:#e3e3e3;
  --paper:#ffffff;
  --link:#0a66c2;
}
*{margin:0;padding:0;box-sizing:border-box}
html,body{width:1200px;height:2567px;overflow:hidden}
body{position:relative;background:var(--page);font-family:"Open Sans",sans-serif;color:var(--ink)}
.abs{position:absolute}
.arabic{font-family:"Noto Sans Arabic","Open Sans",sans-serif;line-height:inherit}

/* stage */
.stage{left:0;top:0;width:1200px;height:930px;background:var(--stage)}

/* brand name (stands in for the logo) */
.brand{display:flex;align-items:center;gap:8px;font-family:"Open Sans",sans-serif;font-weight:600;letter-spacing:.5px;white-space:nowrap}
.brand .dot{display:inline-block;border-radius:50%}

/* business cards */
.card{width:520px;height:300px;box-shadow:0 10px 30px rgba(0,0,0,.45);overflow:hidden}
.card-front{left:50px;top:315px;background:linear-gradient(135deg,var(--blue-dark),var(--blue-light))}
.card-front .brand{position:absolute;left:0;right:0;top:132px;justify-content:center;color:#fff;font-size:24px}
.card-front .brand .dot{width:22px;height:22px;background:#fff}
.card-back{left:630px;top:315px;background:var(--paper)}
.card-back .brand{position:absolute;right:30px;top:34px;color:var(--blue);font-size:15px}
.card-back .brand .dot{width:14px;height:14px;background:var(--blue)}
.card-name{left:30px;top:92px;font-size:19px;line-height:24px;font-weight:700;color:var(--blue);white-space:nowrap}
.card-title{left:30px;top:118px;font-size:13px;line-height:18px;font-weight:600;color:var(--muted)}
.card-ar{left:30px;top:142px;font-size:12px;line-height:19px;color:var(--muted);direction:rtl;text-align:left}
.card-contact{left:30px;top:204px;font-size:12.5px;line-height:19px;color:var(--muted)}
.card-en{right:30px;top:200px;font-size:12.5px;line-height:18px;color:var(--muted);text-align:right}
.row{display:flex;align-items:center;gap:6px}
.row svg{flex:none}

/* bottom bands */
.band{left:0;right:0;bottom:0;height:8px;background:var(--grey-band)}
.band .blue{position:absolute;left:0;top:0;bottom:0;background:var(--blue);clip-path:polygon(0 0,100% 0,calc(100% - 6px) 100%,0 100%)}

/* letterheads */
.letter{top:1043px;background:var(--paper);box-shadow:0 6px 18px rgba(0,0,0,.18);overflow:hidden}
.letter-a{left:165px;width:413px;height:575px}
.letter-b{left:615px;width:408px;height:575px}
.letter .brand{position:absolute;left:37px;top:62px;font-size:8.5px;color:var(--blue)}
.letter .brand .dot{width:12px;height:12px;background:var(--blue)}
.letter-head{right:38px;top:42px;font-size:8.5px;line-height:11.5px;color:#444}
.letter-body{left:37px;right:37px;top:149px;font-size:7px;line-height:11px;color:#555;text-align:justify}
.letter-body p{margin-bottom:11px}
.letter-body .greet{margin-bottom:11px}
.letter-body .close{margin-top:22px}
.letter-sign{left:37px;top:412px;width:50px;height:45px}
.letter .band{height:8px}

/* profile */
.profile{left:227px;top:1760px;width:750px;height:370px;background:var(--paper);box-shadow:0 6px 18px rgba(0,0,0,.2)}
.profile-cover{left:0;top:0;width:750px;height:208px;background:linear-gradient(90deg,#8ea3d4 0%,#9fb0dc 45%,#6f86c5 75%,#4b66b3 100%)}
.profile-photo{left:33px;top:103px;width:150px;height:150px;border-radius:50%;background:radial-gradient(circle at 50% 45%,#d9d2cc,#b9b2ad);border:4px solid #fff;box-shadow:0 0 0 3px #cfd3da}
.btn{top:218px;height:28px;font-family:"Roboto",sans-serif;font-size:14px;display:flex;align-items:center;justify-content:center}
.btn-message{left:546px;width:99px;background:var(--link);color:#fff;font-weight:700;gap:5px}
.btn-more{left:653px;width:70px;border:1px solid #999;color:#777}
.profile-name{left:21px;top:266px;font-family:"Roboto",sans-serif;font-size:17px;line-height:24px;font-weight:500;color:#222;white-space:nowrap}
.profile-name small{font-size:14px;color:#444}
.profile-meta{left:21px;top:294px;font-family:"Roboto",sans-serif;font-size:14px;line-height:22px;color:#222}
.profile-meta a{color:var(--link);text-decoration:none}
.profile-links{left:509px;top:266px;font-family:"Roboto",sans-serif;font-size:13px;line-height:30px;color:#444}
.badge{width:20px;height:20px;border-radius:3px;flex:none}
.profile-links .row{gap:14px}

/* email signature */
.signature{left:178px;top:2182px;width:848px;height:285px;background:var(--paper);box-shadow:0 6px 18px rgba(0,0,0,.2);overflow:hidden;font-family:"Roboto",sans-serif}
.sig-name{left:55px;top:45px;font-size:27px;line-height:32px;font-weight:700;color:var(--blue);white-space:nowrap}
.sig-title{left:55px;top:75px;font-size:20px;line-height:24px;color:var(--muted)}
.sig-ar{left:55px;top:110px;font-size:19px;line-height:29px;color:var(--muted);direction:rtl;text-align:left}
.sig-contact{left:55px;top:173px;font-size:20px;line-height:26px;color:var(--muted)}
.sig-en{right:55px;top:200px;font-size:20px;line-height:26px;color:var(--muted);text-align:right}
.signature .band{height:16px}
</style>
</head>
<body>

<div class="abs stage">
  <section class="abs card card-front" aria-label="Business card front">
    <div class="brand"><span class="dot"></span>QAMAR DATA SYSTEMS</div>
  </section>

  <section class="abs card card-back" aria-label="Business card back">
    <div class="brand"><span class="dot"></span>QAMAR DATA SYSTEMS</div>
    <div class="abs card-name">Karim Haddad <span class="arabic">(كريم حداد)</span></div>
    <div class="abs card-title">Business Development Director</div>
    <div class="abs card-ar arabic">برج النور الدور 12<br>شارع النخيل الحمراء<br>المملكة العربية السعودية</div>
    <div class="abs card-contact">
      <div class="row"><svg width="12" height="12" viewBox="0 0 12 12"><path d="M2 1h2.5l1 2.5-1.3 1a6 6 0 0 0 3.3 3.3l1-1.3 2.5 1V10a1 1 0 0 1-1 1A9 9 0 0 1 1 2a1 1 0 0 1 1-1z" fill="#1a73c4"/></svg>+96 6500 010 234</div>
      <div class="row"><svg width="12" height="12" viewBox="0 0 12 12"><rect x="1" y="2.5" width="10" height="7" fill="#1a73c4"/><path d="M1 2.5l5 4 5-4" stroke="#fff" fill="none"/></svg>info@qamarsys.com</div>
      <div class="row"><svg width="12" height="12" viewBox="0 0 12 12"><circle cx="6" cy="6" r="5" fill="#1a73c4"/><path d="M1 6h10M6 1c-2 3-2 7 0 10M6 1c2 3 2 7 0 10" stroke="#fff" stroke-width=".8" fill="none"/></svg>www.qamarsys.com</div>
    </div>
    <div class="abs card-en">Nour tower 12th floor<br>Palm st. Al Hamra<br>Saudi Arabia</div>
    <div class="abs band"><div class="blue" style="width:68%"></div></div>
  </section>
</div>

<section class="abs letter letter-a" aria-label="Letterhead">
  <div class="brand"><span class="dot"></span>QAMAR DATA SYSTEMS</div>
  <div class="abs letter-head">42 Cedar Lane, Northfield<br>B.C. Canada V0X 1A0<br>☎ 555.010.2040<br>✉ hello@qamarmail.com<br>◍ www.qamarweb.com</div>
  <div class="abs letter-body">
    <p class="greet">Dear customer,</p>
    <p>Thank you for your continued interest in our services and for the trust you have placed in our team over the past year. We are pleased to share an update on our latest projects, the new tools we have introduced and the support our specialists can offer to your organisation. Our aim is to make every step simple, clear and reliable for you. Please reach out at any time if you would like to arrange a meeting to discuss your needs in more detail with us.</p>
    <p>Thank you for your continued interest in our services and for the trust you have placed in our team over the past year. We are pleased to share an update on our latest projects, the new tools we have introduced and the support our specialists can offer to your organisation. Our aim is to make every step simple, clear and reliable for you. Please reach out at any time if you would like to arrange a meeting to discuss your needs in more detail with us.</p>
    <p>Thank you for your continued interest in our services and for the trust you have placed in our team over the past year. We are pleased to share an update on our latest projects, the new tools we have introduced and the support our specialists can offer to your organisation. Our aim is to make every step simple, clear and reliable for you. Please reach out at any time if you would like to arrange a meeting to discuss your needs in more detail with us.</p>
    <p class="close">Yours Sincerely,</p>
  </div>
  <svg class="abs letter-sign" viewBox="0 0 50 45"><path d="M4 14c6-4 10 4 8 16-1 8-6 10-5 2 1-9 8-18 10-10 1 5-1 10 3 6 3-4 4-10 7-6 2 3 0 8 4 4 2-3 5-8 6-4 1 5-2 9 2 7" stroke="#222" stroke-width="1.4" fill="none"/></svg>
  <div class="abs band"><div class="blue" style="width:65%"></div></div>
</section>

<section class="abs letter letter-b" aria-label="Letterhead">
  <div class="brand"><span class="dot"></span>QAMAR DATA SYSTEMS</div>
  <div class="abs letter-head">42 Cedar Lane, Northfield<br>B.C. Canada V0X 1A0<br>☎ 555.010.2040<br>✉ hello@qamarmail.com<br>◍ www.qamarweb.com</div>
  <div class="abs letter-body">
    <p class="greet">Dear customer,</p>
    <p>Thank you for your continued interest in our services and for the trust you have placed in our team over the past year. We are pleased to share an update on our latest projects, the new tools we have introduced and the support our specialists can offer to your organisation. Our aim is to make every step simple, clear and reliable for you. Please reach out at any time if you would like to arrange a meeting to discuss your needs in more detail with us.</p>
    <p>Thank you for your continued interest in our services and for the trust you have placed in our team over the past year. We are pleased to share an update on our latest projects, the new tools we have introduced and the support our specialists can offer to your organisation. Our aim is to make every step simple, clear and reliable for you. Please reach out at any time if you would like to arrange a meeting to discuss your needs in more detail with us.</p>
    <p>Thank you for your continued interest in our services and for the trust you have placed in our team over the past year. We are pleased to share an update on our latest projects, the new tools we have introduced and the support our specialists can offer to your organisation. Our aim is to make every step simple, clear and reliable for you. Please reach out at any time if you would like to arrange a meeting to discuss your needs in more detail with us.</p>
    <p class="close">Yours Sincerely,</p>
  </div>
  <svg class="abs letter-sign" viewBox="0 0 50 45"><path d="M4 14c6-4 10 4 8 16-1 8-6 10-5 2 1-9 8-18 10-10 1 5-1 10 3 6 3-4 4-10 7-6 2 3 0 8 4 4 2-3 5-8 6-4 1 5-2 9 2 7" stroke="#222" stroke-width="1.4" fill="none"/></svg>
  <div class="abs band"><div class="blue" style="width:65%"></div></div>
</section>

<section class="abs profile" aria-label="Professional profile header">
  <div class="abs profile-cover" role="img" aria-label="Cover image: hand holding a phone with contact icons on a blue background"></div>
  <div class="abs profile-photo" role="img" aria-label="Profile photo of Karim Haddad"></div>
  <div class="abs btn btn-message"><svg width="11" height="12" viewBox="0 0 11 12"><rect x="1" y="5" width="9" height="6" fill="#fff"/><path d="M3 5V3.5a2.5 2.5 0 0 1 5 0V5" stroke="#fff" stroke-width="1.4" fill="none"/></svg>Message</div>
  <div class="abs btn btn-more">More...</div>
  <div class="abs profile-name">Karim Haddad <span class="arabic">(كريم حداد)</span> <small>· 2nd</small></div>
  <div class="abs profile-meta">Business Development Director<br>Saudi Arabia · 500+ connections · <a>Contact info</a></div>
  <div class="abs profile-links">
    <div class="row"><span class="badge" style="background:#1aa39a"></span>Harbor &amp; Lane Legal</div>
    <div class="row"><span class="badge" style="background:#2f5aa8"></span>Westbridge University</div>
  </div>
</section>

<section class="abs signature" aria-label="Email signature">
  <div class="abs sig-name">OMAR FARSI <span class="arabic" style="font-weight:600">(عمر فارسي)</span></div>
  <div class="abs sig-title">Managing Director</div>
  <div class="abs sig-ar arabic">42 شارع الأرز، نورثفيلد<br>كندا V0X 1A0</div>
  <div class="abs sig-contact">
    <div class="row"><svg width="18" height="18" viewBox="0 0 12 12"><path d="M2 1h2.5l1 2.5-1.3 1a6 6 0 0 0 3.3 3.3l1-1.3 2.5 1V10a1 1 0 0 1-1 1A9 9 0 0 1 1 2a1 1 0 0 1 1-1z" fill="#1a73c4"/></svg>555.010.2040</div>
    <div class="row"><svg width="18" height="18" viewBox="0 0 12 12"><rect x="1" y="2.5" width="10" height="7" fill="#1a73c4"/><path d="M1 2.5l5 4 5-4" stroke="#fff" fill="none"/></svg>hello@qamarmail.com</div>
    <div class="row"><svg width="18" height="18" viewBox="0 0 12 12"><circle cx="6" cy="6" r="5" fill="#1a73c4"/><path d="M1 6h10M6 1c-2 3-2 7 0 10M6 1c2 3 2 7 0 10" stroke="#fff" stroke-width=".8" fill="none"/></svg>www.qamarweb.com</div>
  </div>
  <div class="abs sig-en">42 Cedar Lane, Northfield<br>B.C. Canada V0X 1A0</div>
  <div class="abs band"><div class="blue" style="width:65%"></div></div>
</section>

</body>
</html>
```